Business Card for Health Food Store

I need a business card for a health food store that includes the following information.

=========
FRONT
=========

***White background***

Bright Harvest (logo)
Supplements - Health Foods - Remedies

2214 Alder Rd.
Willow Bend, CA 95012
(corner of Ferris Ln.)

707-482-3196

BrightHarvest.co
BrightHarvestGoods@mailbox-example.com

On the right side of the front of the card, use a circle type seal with 25 large in the middle. Put the dates below it.
"Celebrating 25 Years"
1997 - 2022

*DO NOT USE A PERSON'S NAME ON THE CARD*

==========
BACK
==========

***Green background***

Full logo in white along with the social logos and handles.

FB Logo / BrightHarvestShop
IG Logo / BrightHarvestShop
Twitter Logo / VisitBrightHarvest

When done I'll need the file in PSD and AI.

Target Market(s)

Surrounding local community

Industry/Entity Type

Retail Health Food Store

Contact Information for Business Card

See brief

Requirements
Must have
• Must be double-sided

```html
<!DOCTYPE html>
<html lang="en">
<head>
<meta charset="utf-8">
<title>Bright Harvest – Business Card</title>
<link rel="stylesheet" href="https://fonts.googleapis.com/css2?family=Montserrat:wght@800&family=Roboto+Condensed:wght@700&family=Arimo:wght@400&display=swap">
<style>
  :root {
    --stage: #2b2b2b;
    --leaf-green: #4cb91a;
    --ink: #0d0d0d;
    --paper: #ffffff;
    --band: #000000;
  }
  * { box-sizing: border-box; margin: 0; padding: 0; }
  html, body { width: 1200px; height: 1015px; overflow: hidden; }
  body {
    background: var(--stage);
    position: relative;
    font-family: "Arimo", Arial, sans-serif;
  }
  .card {
    position: absolute;
    left: 250px;
    width: 700px;
    height: 400px;
    overflow: hidden;
  }
  .card--back { top: 88px; background: var(--leaf-green); }
  .card--front { top: 528px; background: var(--paper); }

  /* Brand lockup */
  .brand-name {
    font-family: "Montserrat", Arial, sans-serif;
    font-weight: 800;
    letter-spacing: -1px;
    line-height: 1;
    white-space: nowrap;
  }
  .brand-tagline {
    font-family: "Roboto Condensed", Arial, sans-serif;
    font-weight: 700;
    text-transform: uppercase;
    letter-spacing: 1.2px;
    white-space: nowrap;
  }

  /* Back */
  .back-lockup {
    position: absolute;
    top: 100px;
    left: 0;
    right: 0;
    text-align: center;
    color: var(--paper);
  }
  .back-lockup .brand-name { font-size: 58px; }
  .back-lockup .brand-tagline { font-size: 17px; margin-top: 6px; }
  .social-band {
    position: absolute;
    left: 0; right: 0;
    top: 282px;
    height: 78px;
    background: var(--band);
    display: flex;
    align-items: center;
    justify-content: space-around;
    padding: 0 40px;
  }
  .social-handle {
    display: flex;
    align-items: center;
    gap: 8px;
    color: var(--paper);
    font-size: 19px;
  }
  .social-dot {
    width: 24px; height: 24px;
    border-radius: 50%;
    background: var(--paper);
  }

  /* Front */
  .front-lockup {
    position: absolute;
    top: 72px;
    left: 50px;
  }
  .front-lockup .brand-name { font-size: 44px; color: var(--ink); }
  .front-lockup .brand-tagline { font-size: 14px; color: var(--leaf-green); margin-top: 4px; }

  .contact-list {
    position: absolute;
    left: 70px;
    color: var(--ink);
    font-size: 18px;
    line-height: 1.25;
  }
  .contact-list--address { top: 196px; }
  .contact-list--reach { top: 284px; }
  .contact-row { display: flex; align-items: center; gap: 10px; }
  .contact-row--top { align-items: flex-start; }
  .contact-icon { width: 16px; height: 16px; flex: none; fill: var(--leaf-green); }
  .contact-row--top .contact-icon { margin-top: 12px; }

  .anniversary {
    position: absolute;
    right: 40px;
    top: 36px;
    width: 240px;
    text-align: center;
  }
  .anniversary-seal { width: 220px; height: 220px; display: block; margin: 0 auto; }
  .anniversary-caption { color: var(--ink); font-size: 18px; margin-top: 18px; }
  .anniversary-years { color: var(--leaf-green); font-size: 18px; }
</style>
</head>
<body>

<section class="card card--back" aria-label="Card back">
  <div class="back-lockup">
    <div class="brand-name">Bright Harvest</div>
    <div class="brand-tagline">Supplements • Health Foods • Remedies</div>
  </div>
  <div class="social-band">
    <div class="social-handle">
      <span class="social-dot"></span><span class="social-dot"></span>
      <span>/BrightHarvestShop</span>
    </div>
    <div class="social-handle">
      <span class="social-dot"></span>
      <span>/ VisitBrightHarvest</span>
    </div>
  </div>
</section>

<section class="card card--front" aria-label="Card front">
  <div class="front-lockup">
    <div class="brand-name">Bright Harvest</div>
    <div class="brand-tagline">Supplements • Health Foods • Remedies</div>
  </div>

  <div class="contact-list contact-list--address">
    <div class="contact-row contact-row--top">
      <svg class="contact-icon" viewBox="0 0 16 16" aria-hidden="true"><path d="M8 0a5.5 5.5 0 0 0-5.5 5.5C2.5 9.6 8 16 8 16s5.5-6.4 5.5-10.5A5.5 5.5 0 0 0 8 0zm0 7.6a2.1 2.1 0 1 1 0-4.2 2.1 2.1 0 0 1 0 4.2z"/></svg>
      <div>2214 Alder Rd.<br>Willow Bend, CA 95012</div>
    </div>
  </div>

  <div class="contact-list contact-list--reach">
    <div class="contact-row">
      <svg class="contact-icon" viewBox="0 0 16 16" aria-hidden="true"><path d="M3.6 1l2.4 3.2-1.5 1.6a9 9 0 0 0 5.7 5.7l1.6-1.5L15 12.4 13.4 15C6.5 15 1 9.5 1 2.6z"/></svg>
      <span>707-482-3196</span>
    </div>
    <div class="contact-row">
      <svg class="contact-icon" viewBox="0 0 16 16" aria-hidden="true"><path d="M8 0a8 8 0 1 0 0 16A8 8 0 0 0 8 0zm5.9 7h-2.5a12 12 0 0 0-1.1-4.8A6 6 0 0 1 13.9 7zM8 2.1c.7.9 1.3 2.7 1.4 4.9H6.6C6.7 4.8 7.3 3 8 2.1zM5.7 2.2A12 12 0 0 0 4.6 7H2.1a6 6 0 0 1 3.6-4.8zM2.1 9h2.5a12 12 0 0 0 1.1 4.8A6 6 0 0 1 2.1 9zM8 13.9c-.7-.9-1.3-2.7-1.4-4.9h2.8c-.1 2.2-.7 4-1.4 4.9zm2.3-.1A12 12 0 0 0 11.4 9h2.5a6 6 0 0 1-3.6 4.8z"/></svg>
      <span>BrightHarvest.com</span>
    </div>
    <div class="contact-row">
      <svg class="contact-icon" viewBox="0 0 16 16" aria-hidden="true"><path d="M0 3h16v10H0zM1.5 4.2v.4L8 9l6.5-4.4v-.4z"/></svg>
      <span>BrightHarvestGoods@mailbox-example.com</span>
    </div>
  </div>

  <div class="anniversary">
    <svg class="anniversary-seal" viewBox="0 0 220 220" role="img" aria-label="Round anniversary seal with the number 25">
      <circle cx="110" cy="110" r="104" fill="none" stroke="var(--leaf-green)" stroke-width="4"/>
      <circle cx="110" cy="110" r="96" fill="none" stroke="var(--leaf-green)" stroke-width="2"/>
      <circle cx="110" cy="110" r="84" fill="none" stroke="var(--leaf-green)" stroke-width="5"/>
      <text x="110" y="140" text-anchor="middle" font-family="Montserrat, Arial, sans-serif" font-weight="800" font-size="88" fill="var(--leaf-green)">25</text>
    </svg>
    <div class="anniversary-caption">Celebrating 25 Years</div>
    <div class="anniversary-years">1997 - 2022</div>
  </div>
</section>

</body>
</html>
```